Keystone Polished Concrete & Grinding
I'm looking for a business card and logo design for my
new Polished Concrete & Grinding business,
If you were to look up Keystone in the dictionary it would
say, first in importance, order, or position; leading.
Polished Concrete floors are a niche market, that are being used currently in Shopping centres, office spaces and by most high end architects, builders and designers.
i need my business card & logo to stand out from my
competitors, i need my design + logo to reflect this it
needs to be simple, professional, eye catching, easy
to read and scream quality. The logo will need to be
suitable for a whole range of applications including,
uniforms, letter heads, stickers, and eventually
incorporating in vehicle vinyl wrapping.
Target Market(s)
Builders, architects, Interior designers & home owners
Contact Information for Business Card
Front side:
- Keystone Polished Concrete & Grinding.
- Logo
Rear side:
- Liam Varesko
- 0438175092
- info@keystonepcg-example.com.au
- commercial - domestic - industrial
- (later down the line website & space for
social media links
www.keystonepolishedslab-example.com.au)
Colors
Designer to choose colors to be used in the design.
Look and feel
Each slider illustrates characteristics of the customer's brand and the style your logo design should communicate.

```html
<!DOCTYPE html>
<html lang="en">
<head>
<meta charset="utf-8">
<title>Keystone Polished Concrete &amp; Grinding – Business Card</title>
<link href="https://fonts.googleapis.com/css2?family=Roboto:wght@400;500&display=swap" rel="stylesheet">
<style>
  :root {
    --backdrop: #1b1b1b;
    --card: #262626;
    --card-edge: #2e2e2e;
    --accent: #29a8e0;
    --text-light: #f2f2f2;
    --text-muted: #d6d6d6;
  }
  * { margin: 0; padding: 0; box-sizing: border-box; }
  html, body {
    width: 1200px; height: 900px; overflow: hidden;
    background: var(--backdrop);
    font-family: "Roboto", Arial, sans-serif;
  }
  .canvas {
    width: 1200px; height: 900px;
    display: flex; flex-direction: column; align-items: center; justify-content: center;
    gap: 40px;
  }
  .card {
    position: relative;
    width: 680px; height: 388px;
    background: linear-gradient(135deg, var(--card) 0%, var(--card-edge) 100%);
    border-bottom: 6px solid var(--accent);
    box-shadow: 0 12px 30px rgba(0,0,0,0.55);
    overflow: hidden;
  }
  .brand-name {
    color: var(--accent);
    font-weight: 500;
    text-transform: uppercase;
    text-align: center;
    line-height: 1.2;
  }
  /* Front */
  .card-front .brand-name {
    position: absolute; left: 0; right: 0; top: 128px;
    font-size: 30px; letter-spacing: 2px;
  }
  .card-front .brand-name .brand-sub {
    display: block; font-size: 17px; letter-spacing: 3px; margin-top: 6px;
  }
  .services {
    position: absolute; left: 0; right: 0; bottom: 28px;
    text-align: center;
    color: var(--text-light);
    font-size: 15px; letter-spacing: 1px;
  }
  /* Back */
  .card-back .brand-name {
    position: absolute; left: 30px; top: 148px; width: 250px;
    font-size: 24px; letter-spacing: 1.5px;
  }
  .card-back .brand-name .brand-sub {
    display: block; font-size: 13px; letter-spacing: 2px; margin-top: 6px;
  }
  .divider {
    position: absolute; left: 305px; top: 92px;
    width: 2px; height: 180px; background: var(--accent);
  }
  .contact-block {
    position: absolute; left: 336px; top: 96px; width: 330px;
  }
  .person-name {
    color: var(--accent);
    font-size: 32px; font-weight: 500; letter-spacing: 3px;
    text-transform: uppercase;
  }
  .person-role {
    color: var(--text-light);
    font-size: 16px; margin-top: 2px;
  }
  .contact-list { list-style: none; margin-top: 26px; }
  .contact-item {
    display: flex; align-items: center; gap: 10px;
    color: var(--text-muted);
    font-size: 15px; margin-bottom: 9px;
  }
  .contact-icon { width: 13px; height: 13px; flex: none; }
</style>
</head>
<body>
<main class="canvas">
  <section class="card card-front">
    <p class="brand-name">Keystone Polished<span class="brand-sub">Concrete &amp; Grinding</span></p>
    <p class="services">COMMERCIAL - DOMESTIC - INDUSTRIAL</p>
  </section>

  <section class="card card-back">
    <p class="brand-name">Keystone Polished<span class="brand-sub">Concrete &amp; Grinding</span></p>
    <div class="divider"></div>
    <div class="contact-block">
      <h1 class="person-name">Liam Varesko</h1>
      <p class="person-role">Director</p>
      <ul class="contact-list">
        <li class="contact-item">
          <svg class="contact-icon" viewBox="0 0 16 16" aria-hidden="true"><path fill="#29a8e0" d="M3.6 1.5l2.3 2.4-1.3 2c.9 1.9 2.4 3.4 4.3 4.3l2-1.3 2.4 2.3-1.3 2.3C7 13.3 2.7 9 2.3 2.8z"/></svg>
          <span>0438175092</span>
        </li>
        <li class="contact-item">
          <svg class="contact-icon" viewBox="0 0 16 16" aria-hidden="true"><rect x="1.5" y="3.5" width="13" height="9" fill="none" stroke="#29a8e0" stroke-width="1.4"/><path d="M1.5 3.5l6.5 5 6.5-5" fill="none" stroke="#29a8e0" stroke-width="1.4"/></svg>
          <span>info@keystonepcg-example.com.au</span>
        </li>
        <li class="contact-item">
          <svg class="contact-icon" viewBox="0 0 16 16" aria-hidden="true"><circle cx="8" cy="8" r="6.3" fill="none" stroke="#29a8e0" stroke-width="1.3"/><ellipse cx="8" cy="8" rx="2.8" ry="6.3" fill="none" stroke="#29a8e0" stroke-width="1.1"/><path d="M1.7 8h12.6M2.6 5h10.8M2.6 11h10.8" stroke="#29a8e0" stroke-width="1"/></svg>
          <span>www.keystonepolishedslab-example.com.au</span>
        </li>
      </ul>
    </div>
  </section>
</main>
</body>
</html>
```